W need a Menu Board designed for a" make your own poke bowl" and Sushi Menu. We would like our logo & Colors to be intergraded with the menu . Also will need to be able to adjust the pricing in the future as needed.

```html
<!DOCTYPE html>
<html lang="en">
<head>
<meta charset="utf-8">
<title>Tideline Food Menu</title>
<link rel="stylesheet" href="https://fonts.googleapis.com/css2?family=Bungee&family=Montserrat:wght@400;500;700;800&family=Archivo+Narrow:wght@400&display=swap">
<style>
:root{
  --blue:#1f4fa8;
  --blue-soft:#5a8fd6;
  --ink:#1d1d1f;
  --paper:#f3f4f6;
  --paper-2:#e7e9ec;
  --page:#e9e9ea;
  --rule:#1f4fa8;
  --photo-wood:#c9a46a;
  --photo-dark:#3b4a3a;
}
*{box-sizing:border-box;margin:0;padding:0}
html,body{width:1200px;height:2293px;overflow:hidden;background:var(--page)}
body{position:relative;font-family:"Montserrat",sans-serif;color:var(--ink)}
.menu-board{
  position:absolute;left:40px;top:353px;width:1061px;height:1503px;
  transform:scale(1.0556);transform-origin:0 0;
  background:linear-gradient(180deg,var(--paper) 0%,#fafafa 40%,var(--paper-2) 100%);
  box-shadow:0 4px 14px rgba(0,0,0,.25);overflow:hidden;
}
.abs{position:absolute}
.photo{position:absolute;border-radius:6px}
.photo-sushi-board{left:10px;top:10px;width:265px;height:235px;background:linear-gradient(135deg,var(--photo-wood),#eee 60%,#c9c9c9);transform:rotate(-8deg)}
.photo-sushi-platter{left:840px;top:10px;width:221px;height:275px;background:linear-gradient(160deg,#d9c7a8,#e07a3c 50%,#2c2c2c)}
.photo-seaweed{left:460px;top:1240px;width:345px;height:263px;background:radial-gradient(circle at 45% 55%,#3f7d2a 0,#6f9c3a 30%,#f5f5f5 55%,#b9bec6 100%)}
.photo-poke-bowl{left:820px;top:1245px;width:241px;height:258px;background:radial-gradient(circle at 55% 55%,#e99a3a 0,#7d4a8f 35%,#2f5a33 70%,#1d2a1d 100%)}
.doodle-band{top:718px;height:72px;background:linear-gradient(90deg,rgba(170,175,185,.35),rgba(170,175,185,.15))}
.doodle-left{left:0;width:320px}
.doodle-right{left:740px;width:321px}

.brand{left:0;width:1061px;top:80px;text-align:center;font-weight:800;font-size:82px;letter-spacing:4px;color:var(--blue);line-height:1}
.brand-mark{display:inline-block;width:22px;height:22px;border-radius:50%;background:var(--blue);margin-right:14px;vertical-align:middle}
.title-banner{left:288px;top:212px;width:509px;height:88px;background:var(--blue);border-radius:10px;display:flex;align-items:center;justify-content:center;box-shadow:inset 0 0 0 4px #fff,0 0 0 3px var(--blue)}
.title-banner h1{font-family:"Bungee",sans-serif;color:#fff;font-size:58px;letter-spacing:3px;font-weight:400}

.section-title{font-family:"Bungee",sans-serif;color:var(--blue);font-size:24px;font-weight:400;letter-spacing:1px}
.icon-chip{display:inline-block;vertical-align:middle;margin-left:10px}

.item-list{position:absolute;list-style:none}
.item{display:flex;align-items:flex-start;font-size:16px;line-height:19px;margin-bottom:6px}
.item::before{content:"";flex:none;width:13px;height:7px;margin:6px 12px 0 0;border-radius:3px 3px 1px 1px;background:var(--blue-soft)}
.item-name{flex:none;max-width:130px}
.item-name small{display:block;font-family:"Archivo Narrow",sans-serif;font-size:12.5px;line-height:19px}
.leader{flex:1;border-top:1px solid var(--ink);margin:10px 6px 0;min-width:10px}
.price{flex:none;background:var(--blue-soft);color:#fff;font-size:13px;font-weight:500;padding:1px 4px;border-radius:3px;line-height:17px}
.price sup{font-size:8px}

.plain-list{position:absolute;list-style:none;font-size:16px;line-height:25px}
.poke-title{left:0;width:1061px;top:733px;text-align:center}
.poke-title .section-title{font-size:28px}
.bowl-icon{display:inline-block;width:38px;height:30px;vertical-align:middle;margin:0 22px}
.start-price{left:398px;top:773px;height:27px;display:flex;border:2px solid var(--blue-soft);font-size:19px}
.start-price span{padding:0 8px;color:var(--blue);letter-spacing:1px;line-height:23px}
.start-price b{background:var(--blue-soft);color:#fff;padding:0 8px;line-height:23px;font-weight:700}

.choice-head{font-size:21px;border-bottom:1.5px solid var(--blue);padding-bottom:1px;display:inline-block}
.choice-head b{color:var(--blue);font-weight:700}
.cols{display:grid;grid-template-columns:144px auto}
.priced{position:absolute;list-style:none;font-size:16px;line-height:25px}
.priced li{display:flex;align-items:center}
.priced .rule{flex:1;border-top:1px solid var(--rule);margin:4px 8px 0}
</style>
</head>
<body>
<main class="menu-board">
  <div class="photo photo-sushi-board" role="img" aria-label="Photo of assorted sushi rolls on a board with soy sauce and chopsticks"></div>
  <div class="photo photo-sushi-platter" role="img" aria-label="Photo of a sushi platter with salmon rolls and soy sauce"></div>

  <div class="abs brand"><span class="brand-mark"></span>TIDELINE</div>
  <div class="abs title-banner"><h1>FOOD MENU</h1></div>

  <!-- Sushi rolls -->
  <h2 class="abs section-title" style="left:62px;top:350px">SUSHI ROLLS
    <svg class="icon-chip" width="36" height="26" viewBox="0 0 36 26"><rect x="2" y="6" width="14" height="16" rx="6" fill="#111"/><rect x="20" y="4" width="14" height="16" rx="6" fill="#111"/><ellipse cx="9" cy="8" rx="5" ry="2.5" fill="#fff"/><ellipse cx="27" cy="6" rx="5" ry="2.5" fill="#fff"/></svg>
  </h2>
  <ul class="item-list" style="left:62px;top:398px;width:220px">
    <li class="item"><span class="item-name">Tuna Tartar</span><span class="leader"></span><span class="price"><sup>$</sup>24.99</span></li>
    <li class="item"><span class="item-name">Salmon Tartar</span><span class="leader"></span><span class="price"><sup>$</sup>22.99</span></li>
    <li class="item"><span class="item-name">Tuna Tower</span><span class="leader"></span><span class="price"><sup>$</sup>16.99</span></li>
    <li class="item"><span class="item-name">Salmon Tower</span><span class="leader"></span><span class="price"><sup>$</sup>16.99</span></li>
    <li class="item"><span class="item-name">Kani Salad</span><span class="leader"></span><span class="price"><sup>$</sup>18.99</span></li>
    <li class="item"><span class="item-name">Kali Roll <small style="display:inline">(Inside Out</small><small>w/ Kani, Cucumber, Avocado, &amp; Tempura Flakes Topped w/ Salmon &amp; ressed with Eel Sauce)</small></span><span class="leader"></span><span class="price"><sup>$</sup>14.99</span></li>
    <li class="item"><span class="item-name">Tuna Avocado w/ Salmon on Top</span><span class="leader"></span><span class="price"><sup>$</sup>14.99</span></li>
  </ul>
  <ul class="item-list" style="left:337px;top:398px;width:230px">
    <li class="item"><span class="item-name">Tuna Tataki</span><span class="leader"></span><span class="price"><sup>$</sup>18.99</span></li>
    <li class="item"><span class="item-name">California Roll</span><span class="leader"></span><span class="price"><sup>$</sup>9.99</span></li>
    <li class="item"><span class="item-name">Avocado Roll</span><span class="leader"></span><span class="price"><sup>$</sup>7.99</span></li>
    <li class="item"><span class="item-name" style="max-width:150px">Tuna Roll (Small)</span><span class="leader"></span><span class="price"><sup>$</sup>9.99</span></li>
    <li class="item"><span class="item-name">Salmon Roll (Small)</span><span class="leader"></span><span class="price"><sup>$</sup>9.99</span></li>
    <li class="item"><span class="item-name" style="max-width:145px">Salmon Avocado w/ Tuna on Top</span><span class="leader"></span><span class="price"><sup>$</sup>14.99</span></li>
    <li class="item"><span class="item-name">Tuna Avocado w/ Tuna on Top</span><span class="leader"></span><span class="price"><sup>$</sup>14.99</span></li>
  </ul>
  <ul class="item-list" style="left:618px;top:398px;width:227px">
    <li class="item"><span class="item-name">Cucumber Roll</span><span class="leader"></span><span class="price"><sup>$</sup>7.99</span></li>
    <li class="item"><span class="item-name">Veggie Roll</span><span class="leader"></span><span class="price"><sup>$</sup>9.99</span></li>
    <li class="item"><span class="item-name" style="max-width:140px">Salmon Avocado Roll</span><span class="leader"></span><span class="price"><sup>$</sup>9.99</span></li>
    <li class="item"><span class="item-name" style="max-width:140px">Salmon Avocado w/ Salmon on Top</span><span class="leader"></span><span class="price"><sup>$</sup>14.99</span></li>
    <li class="item"><span class="item-name" style="max-width:140px">Rikki Roll <small style="display:inline">(Inside Out</small><small>w/ Kani, Cucumber &amp; Cilantro Topped w/ Hamachi, Jalapeno &amp; Dressed w/ Cilantro Truffle Sauce)</small></span><span class="leader"></span><span class="price"><sup>$</sup>15.99</span></li>
    <li class="item"><span class="item-name">Spicy Tuna Roll</span><span class="leader"></span><span class="price"><sup>$</sup>9.99</span></li>
  </ul>

  <h2 class="abs section-title" style="left:905px;top:350px">NEGRI</h2>
  <ul class="plain-list" style="left:906px;top:392px">
    <li>Salmon</li><li>Ahi</li><li>Wahoo</li><li>Hamachi</li><li>Toro</li>
  </ul>

  <!-- Poke bowls -->
  <div class="abs doodle-band doodle-left" role="img" aria-label="Line illustrations of sushi pieces"></div>
  <div class="abs doodle-band doodle-right" role="img" aria-label="Line illustrations of sushi pieces"></div>
  <div class="abs poke-title">
    <svg class="bowl-icon" viewBox="0 0 38 30"><path d="M2 14h34a17 15 0 0 1-34 0z" fill="#5a8fd6"/><ellipse cx="19" cy="13" rx="15" ry="5" fill="#5a8fd6"/><path d="M14 12L24 1M18 12L30 3" stroke="#5a8fd6" stroke-width="2"/></svg>
    <h2 class="section-title" style="display:inline;vertical-align:middle">POKE BOWLS</h2>
    <svg class="bowl-icon" viewBox="0 0 38 30"><path d="M2 14h34a17 15 0 0 1-34 0z" fill="#5a8fd6"/><ellipse cx="19" cy="13" rx="15" ry="5" fill="#5a8fd6"/><path d="M14 12L24 1M18 12L30 3" stroke="#5a8fd6" stroke-width="2"/></svg>
  </div>
  <div class="abs start-price"><span>STARTING PRICE</span><b><sup style="font-size:11px">$</sup>15.99</b></div>

  <h3 class="abs choice-head" style="left:63px;top:848px;font-weight:400">Choice 1 - <b>BASE</b></h3>
  <ul class="plain-list" style="left:65px;top:882px">
    <li>White Rice</li><li>Brown Rice</li><li>Quinoa</li><li>Zucchini Noodles</li><li>Lettuce</li>
  </ul>

  <h3 class="abs choice-head" style="left:384px;top:848px;font-weight:400">Choice 1 - <b>PROTEIN</b></h3>
  <ul class="plain-list cols" style="left:386px;top:882px;grid-template-columns:136px auto">
    <li>Tuna Poke</li><li>Spicy</li><li>Salmon Poke</li><li>Salmon</li><li>Spicy Tuna</li><li>Kani</li>
  </ul>

  <h3 class="abs choice-head" style="left:698px;top:848px"><b>SAUCES</b></h3>
  <ul class="plain-list cols" style="left:701px;top:882px;grid-template-columns:127px auto">
    <li>Spicy Mayo</li><li>Cilantro Garlic Aioli</li><li>Sweet Chili</li><li>Basil Aioli</li><li>Sriracha</li><li>Sesame Ginger</li><li>Ponzu</li><li>Carrot Honey Ginger</li><li>Eel Sauce</li>
  </ul>

  <h3 class="abs choice-head" style="left:62px;top:1041px;font-weight:400">Choice 4 - <b>TOPPINGS</b></h3>
  <ul class="plain-list cols" style="left:65px;top:1075px">
    <li>Asian Slaw</li><li>Carrot</li><li>Edamame</li><li>Radish</li><li>Red Onion</li><li>Cucumber</li><li>Red Cabbage</li><li>Tomato</li><li>Jalapeno</li><li>Sprout</li><li>Scallions</li><li>Cilantro</li><li>Pickled Ginger</li>
  </ul>

  <h3 class="abs choice-head" style="left:386px;top:1041px;font-weight:400">Choice 1 - <b>CRUNCH</b></h3>
  <ul class="plain-list" style="left:388px;top:1075px">
    <li>Tempura Flakes</li><li>Toasted Shredded</li><li>Nori</li>
  </ul>

  <h3 class="abs choice-head" style="left:698px;top:1041px"><b>PREMIUM TOPPINGS</b></h3>
  <ul class="priced" style="left:700px;top:1075px;width:297px">
    <li>White Rice<span class="rule"></span><span class="price"><sup>$</sup>2.00</span></li>
    <li>Brown Rice<span class="rule"></span><span class="price"><sup>$</sup>1.00</span></li>
    <li>Quinoa<span class="rule"></span><span class="price"><sup>$</sup>1.00</span></li>
    <li>Zucchini Noodles<span class="rule"></span><span class="price"><sup>$</sup>1.00</span></li>
    <li>Lettuce<span class="rule"></span><span class="price"><sup>$</sup>1.00</span></li>
  </ul>

  <h3 class="abs choice-head" style="left:64px;top:1280px;border:0"><b>ADDITIONAL PROTEIN SCOOP</b></h3>
  <ul class="priced" style="left:65px;top:1315px;width:297px">
    <li>Tuna Poke<span class="rule"></span><span class="price"><sup>$</sup>4.00</span></li>
    <li>Salmon Poke<span class="rule"></span><span class="price"><sup>$</sup>4.00</span></li>
    <li>Spicy Tuna<span class="rule"></span><span class="price"><sup>$</sup>4.00</span></li>
    <li>Spicy Salmon<span class="rule"></span><span class="price"><sup>$</sup>4.00</span></li>
    <li>Kani<span class="rule"></span><span class="price"><sup>$</sup>4.00</span></li>
  </ul>

  <div class="photo photo-seaweed" role="img" aria-label="Photo of seaweed salad in a white bowl with lemon, chopsticks and soy sauce"></div>
  <div class="photo photo-poke-bowl" role="img" aria-label="Photo of a poke bowl with salmon, edamame, mango, cabbage and rice"></div>
</main>
</body>
</html>
```